Modern Verdell Tree Care Website

I need a website for a full service Tree Care company. The company provides tree pruning, tree removal, tree preservation, emergency services, stump grinding, and emergency tree services.

Target Market(s)

Customers that need tree services

Industry/Entity Type

Landscaping, Tree Services

Coding

Coded - Design and coding required

Number of Pages Required

5+ page

Font styles to use
Sans Serif

Requirements
Must have
• Good clean design that showcases the services the company provides.
Nice to have
• Services page; contact form, blog, home page, about page

```html
<!DOCTYPE html>
<html lang="en">
<head>
<meta charset="utf-8">
<title>Verdell Tree Care</title>
<link href="https://fonts.googleapis.com/css2?family=Audiowide&family=Poppins:wght@400;500;600;700;800&display=swap" rel="stylesheet">
<style>
:root{
  --green:#79b23a;
  --green-dark:#5e8f2a;
  --orange:#f5a21b;
  --ink:#2b2f2d;
  --muted:#6b6f6c;
  --panel:rgba(58,64,60,.82);
  --footer:#3c4241;
  --line:#e3e5e2;
  --white:#ffffff;
}
*{box-sizing:border-box;margin:0;padding:0}
html,body{width:1200px;height:4784px;overflow:hidden}
body{font-family:'Poppins',sans-serif;color:var(--ink);background:var(--white);position:relative}
.section{position:absolute;left:0;width:1200px}
.h-tech{font-family:'Audiowide',sans-serif;font-weight:400;letter-spacing:3px;text-transform:uppercase}
.btn{display:inline-block;font-family:'Poppins',sans-serif;font-size:13px;font-weight:600;color:var(--white);padding:10px 22px;border-radius:3px;text-decoration:none}
.btn-green{background:var(--green)}
.btn-orange{background:var(--orange);color:var(--ink)}
.brand{display:flex;align-items:center;gap:10px;font-family:'Poppins',sans-serif;font-weight:700;text-transform:uppercase;color:var(--green-dark);letter-spacing:1px}
.brand-mark{width:16px;height:16px;background:var(--orange)}
.photo{position:absolute}

/* header */
.site-header{top:0;height:100px;display:flex;align-items:center;justify-content:space-between;padding:0 140px;background:var(--white)}
.site-header .brand{font-size:22px;line-height:1}
.main-nav{display:flex;align-items:center;gap:38px;font-size:14px;font-weight:500}
.main-nav a{color:var(--ink);text-decoration:none}
.main-nav .btn{color:var(--white)}

/* hero */
.hero{top:100px;height:680px;overflow:hidden}
.hero .photo{inset:0;background:linear-gradient(115deg,#6f7a78 0%,#a9b2b4 35%,#8f8a7f 60%,#5f5446 85%,#3f3a30 100%)}
.hero-copy{position:absolute;left:140px;top:48px;color:var(--white)}
.hero-copy h1{font-size:46px;font-weight:800;line-height:1.12;text-transform:uppercase;letter-spacing:.5px}
.hero-copy p{font-size:19px;font-weight:600;margin:14px 0 22px}
.hero-curve{position:absolute;left:0;bottom:0}

/* services */
.services{top:700px;height:640px;text-align:center}
.section-title{font-size:36px;color:#3a3f3c;display:flex;align-items:center;justify-content:center;gap:18px}
.section-title::before,.section-title::after{content:"";width:34px;height:2px;background:var(--green)}
.services .intro{width:600px;margin:24px auto 0;font-size:14px;line-height:1.6;color:var(--muted)}
.service-cards{position:absolute;left:140px;top:210px;width:920px;display:flex;gap:22px;text-align:left}
.service-card{width:215px}
.service-card .thumb{height:180px;position:relative}
.service-card h3{font-size:17px;font-weight:600;margin:16px 0 8px}
.service-card .more{font-size:12px;color:var(--green-dark);font-weight:500;border-bottom:1px solid var(--green);padding-bottom:2px}
.service-card.featured{background:var(--white);box-shadow:0 10px 30px rgba(0,0,0,.15);margin-top:-20px;padding-bottom:22px}
.service-card.featured h3,.service-card.featured p,.service-card.featured .more{margin-left:16px;margin-right:16px}
.service-card.featured p{font-size:12px;line-height:1.5;color:var(--muted);margin-bottom:10px}
.slider-arrow{position:absolute;top:310px;width:30px;height:30px;border-radius:50%;border:2px solid var(--orange);display:flex;align-items:center;justify-content:center}
.slider-arrow.next{background:var(--orange)}
.services .btn{position:absolute;left:532px;top:574px}

/* about */
.about{top:1392px;height:590px}
.about .photo{inset:0;background:linear-gradient(90deg,#2f2a22 0%,#6a5a44 30%,#8b7a5e 50%,#5b6b4a 75%,#34452c 100%)}
.about-panel{position:absolute;left:640px;top:44px;width:480px;height:500px;background:var(--panel);padding:40px 36px;color:var(--white)}
.about-panel h2{font-size:34px;line-height:1.2;display:flex;gap:14px;align-items:flex-start}
.about-panel h2::before{content:"";width:26px;height:2px;background:var(--green);margin-top:20px}
.about-panel p{font-size:13px;line-height:1.75;margin:22px 0 16px;color:#e8ebe7}
.about-panel p + p{margin-top:0}

/* service area */
.area{top:2020px;height:560px}
.area .map{left:100px;top:40px;width:470px;height:450px;background:radial-gradient(circle at 50% 50%,#f2f4f0 0%,#e3e7df 70%,#fff 100%);border-radius:6px}
.area-copy{position:absolute;left:690px;top:110px}
.area-copy h2{font-size:34px;color:#3a3f3c;display:flex;align-items:center;gap:14px}
.area-copy h2::before{content:"";width:26px;height:2px;background:var(--green)}
.area-list{display:grid;grid-template-columns:200px 200px;row-gap:16px;margin:34px 0 30px 40px;font-size:14px;list-style:none}
.area-list li{display:flex;align-items:center;gap:10px}
.area-copy .btn{margin-left:40px}

/* why */
.why{top:2592px;height:520px}
.why .photo{inset:0;background:linear-gradient(100deg,#3d5a2c 0%,#5f7d45 35%,#8fa36c 55%,#c2c9b4 70%,#6f8a52 100%)}
.why-panel{position:absolute;left:140px;top:80px;width:460px;height:320px;background:var(--panel);padding:34px 32px;color:var(--white)}
.why-panel h2{font-size:30px}
.why-list{display:grid;grid-template-columns:205px 190px;row-gap:12px;margin:24px 0 28px;list-style:none;font-size:13px}
.why-list li{display:flex;align-items:center;gap:8px}

/* blog */
.blog{top:3160px;height:720px;text-align:center}
.blog .section-title{margin-top:20px}
.post{position:absolute;background:var(--white);box-shadow:0 6px 22px rgba(0,0,0,.12);text-align:left}
.post .thumb{position:absolute}
.post .body{position:absolute}
.post .date{font-size:12px;color:var(--muted);display:flex;align-items:center;gap:6px}
.post h3{font-size:15px;font-weight:600;line-height:1.35;margin:10px 0 10px}
.post p{font-size:12px;line-height:1.55;color:var(--muted)}
.post-a{left:140px;top:120px;width:480px;height:230px}
.post-b{left:140px;top:370px;width:480px;height:230px}
.post-a .thumb,.post-b .thumb{left:0;top:0;width:210px;height:230px}
.post-a .body,.post-b .body{left:232px;top:20px;width:228px}
.post-c{left:660px;top:120px;width:400px;height:480px}
.post-c .thumb{left:0;top:0;width:400px;height:240px}
.post-c .body{left:22px;top:262px;width:356px}
.blog .btn{position:absolute;left:540px;top:632px}

/* contact */
.contact{top:3900px;height:640px}
.contact .photo{inset:0;background:linear-gradient(180deg,#dfe6d8 0%,#eef1ea 50%,#cdd6c2 100%)}
.contact-title{position:absolute;top:30px;font-size:34px;color:#3a3f3c}
.contact-card{position:absolute;left:140px;top:110px;width:440px;height:360px;background:var(--white);box-shadow:0 8px 26px rgba(0,0,0,.14)}
.contact-card .person{position:absolute;left:-10px;top:20px;width:190px;height:340px;background:linear-gradient(180deg,#f3c13a 0%,#e6b64a 18%,#c9a488 40%,#3f6a9b 100%);border-radius:6px}
.contact-info{position:absolute;left:200px;top:30px;width:220px}
.contact-info h4{font-size:13px;font-weight:700;margin-bottom:18px}
.contact-row{display:flex;gap:10px;margin-bottom:18px;font-size:12px;line-height:1.5}
.contact-row .ico{flex:none;width:26px;height:26px;border-radius:50%;background:var(--green);display:flex;align-items:center;justify-content:center}
.inquiry{position:absolute;left:670px;top:110px;width:390px;height:360px;background:rgba(255,255,255,.9);padding:22px}
.field{height:40px;border:1px solid var(--line);background:var(--white);font-size:12px;color:#9a9e9a;padding:11px 14px;margin-bottom:10px}
.field.message{height:90px}

/* footer */
.site-footer{top:4480px;height:304px}
.footer-curve{position:absolute;left:0;top:0}
.footer-inner{position:absolute;left:0;top:60px;width:1200px;height:244px;background:var(--footer);text-align:center;color:var(--white)}
.footer-inner .brand{justify-content:center;color:var(--white);font-size:30px;margin-top:30px}
.footer-nav{display:flex;justify-content:center;gap:40px;font-size:13px;margin-top:40px}
.footer-base{position:absolute;left:140px;right:140px;bottom:22px;display:flex;justify-content:space-between;align-items:center;font-size:11px;color:#c9ccc9;border-top:1px solid rgba(255,255,255,.15);padding-top:16px}
.socials{display:flex;gap:10px}
.socials span{width:22px;height:22px;border-radius:50%;border:1px solid #c9ccc9}
</style>
</head>
<body>

<header class="section site-header">
  <div class="brand"><span class="brand-mark"></span>Verdell Tree Care</div>
  <nav class="main-nav">
    <a href="#">Home</a><a href="#">About Us</a><a href="#">Services</a><a href="#">Blog</a>
    <a class="btn btn-green" href="#">Contact Us</a>
  </nav>
</header>

<section class="section hero">
  <div class="photo" role="img" aria-label="Arborist in safety gear cutting a large tree limb high in the canopy"></div>
  <div class="hero-copy">
    <h1>Expert Tree Care<br>and Landscaping<br>Solutions for You</h1>
    <p>Serving Lafayette &amp; Surrounding Areas</p>
    <a class="btn btn-orange" href="#">Contact Us</a>
  </div>
  <svg class="hero-curve" width="1200" height="140" viewBox="0 0 1200 140">
    <path d="M0 90 Q600 175 1200 20 L1200 140 L0 140 Z" fill="#ffffff"/>
    <path d="M0 86 Q600 170 1200 16" fill="none" stroke="#f5a21b" stroke-width="6"/>
  </svg>
</section>

<section class="section services">
  <h2 class="section-title h-tech">Our Services</h2>
  <p class="intro">Lorem Ipsum is simply dummy text of the printing and typesetting industry. Lorem Ipsum has been the industry's standard dummy text ever since.</p>
  <div class="slider-arrow prev" style="left:86px"><svg width="12" height="12" viewBox="0 0 12 12"><path d="M8 1 L3 6 L8 11" fill="none" stroke="#f5a21b" stroke-width="2"/></svg></div>
  <div class="service-cards">
    <article class="service-card">
      <div class="thumb" role="img" aria-label="Worker pruning tree branches" style="background:linear-gradient(135deg,#5c8a33,#a9c46e)"></div>
      <h3>Tree Pruning</h3><span class="more">Learn More</span>
    </article>
    <article class="service-card featured">
      <div class="thumb" role="img" aria-label="Crew cutting up a felled tree" style="background:linear-gradient(135deg,#6b7e5a,#c9c3a8)"></div>
      <h3>Tree Removal</h3>
      <p>Lorem Ipsum is simply dummy text of the printing and typesetting industry.</p>
      <span class="more">Learn More</span>
    </article>
    <article class="service-card">
      <div class="thumb" role="img" aria-label="Arborist checking the health of a tree" style="background:linear-gradient(135deg,#4f7a35,#8fb05e)"></div>
      <h3>Tree Preservation</h3><span class="more">Learn More</span>
    </article>
    <article class="service-card">
      <div class="thumb" role="img" aria-label="Stump grinding machine at work" style="background:linear-gradient(135deg,#8a5a2a,#e0a040)"></div>
      <h3>Stump Grinding</h3><span class="more">Learn More</span>
    </article>
  </div>
  <div class="slider-arrow next" style="left:1084px"><svg width="12" height="12" viewBox="0 0 12 12"><path d="M4 1 L9 6 L4 11" fill="none" stroke="#ffffff" stroke-width="2"/></svg></div>
  <a class="btn btn-green" href="#">View All Services</a>
</section>

<section class="section about">
  <div class="photo" role="img" aria-label="Worker cutting a tree stump with a chainsaw in the woods"></div>
  <div class="about-panel">
    <h2 class="h-tech">About Verdell<br>Tree Care</h2>
    <p>At Verdell Tree Care, we are more than just a tree service company; we are stewards of your beautiful trees. With a passion deeply rooted in arboriculture, our team is committed to providing top-quality care, safe work and honest pricing for every client.</p>
    <p>Whether you need a tree trimmed, removed or assessed, our skilled crew brings the right equipment and experience to each job. We focus on clean results, careful planning and lasting health for the trees on your property.</p>
    <a class="btn btn-orange" href="#">Contact Us</a>
  </div>
</section>

<section class="section area">
  <div class="photo map" role="img" aria-label="Outline map of the parish with pins marking each service town"></div>
  <div class="area-copy">
    <h2 class="h-tech">Service Area</h2>
    <ul class="area-list">
      <li><svg width="12" height="16" viewBox="0 0 12 16"><path d="M6 0a6 6 0 0 1 6 6c0 4.5-6 10-6 10S0 10.5 0 6a6 6 0 0 1 6-6z" fill="#f5a21b"/><circle cx="6" cy="6" r="2.2" fill="#fff"/></svg>Carencro</li>
      <li><svg width="12" height="16" viewBox="0 0 12 16"><path d="M6 0a6 6 0 0 1 6 6c0 4.5-6 10-6 10S0 10.5 0 6a6 6 0 0 1 6-6z" fill="#f5a21b"/><circle cx="6" cy="6" r="2.2" fill="#fff"/></svg>Duson</li>
      <li><svg width="12" height="16" viewBox="0 0 12 16"><path d="M6 0a6 6 0 0 1 6 6c0 4.5-6 10-6 10S0 10.5 0 6a6 6 0 0 1 6-6z" fill="#79b23a"/><circle cx="6" cy="6" r="2.2" fill="#fff"/></svg><strong>Scott</strong></li>
      <li><svg width="12" height="16" viewBox="0 0 12 16"><path d="M6 0a6 6 0 0 1 6 6c0 4.5-6 10-6 10S0 10.5 0 6a6 6 0 0 1 6-6z" fill="#f5a21b"/><circle cx="6" cy="6" r="2.2" fill="#fff"/></svg>Broussard</li>
      <li><svg width="12" height="16" viewBox="0 0 12 16"><path d="M6 0a6 6 0 0 1 6 6c0 4.5-6 10-6 10S0 10.5 0 6a6 6 0 0 1 6-6z" fill="#f5a21b"/><circle cx="6" cy="6" r="2.2" fill="#fff"/></svg>Judice</li>
      <li><svg width="12" height="16" viewBox="0 0 12 16"><path d="M6 0a6 6 0 0 1 6 6c0 4.5-6 10-6 10S0 10.5 0 6a6 6 0 0 1 6-6z" fill="#f5a21b"/><circle cx="6" cy="6" r="2.2" fill="#fff"/></svg>Youngsville</li>
      <li><svg width="12" height="16" viewBox="0 0 12 16"><path d="M6 0a6 6 0 0 1 6 6c0 4.5-6 10-6 10S0 10.5 0 6a6 6 0 0 1 6-6z" fill="#f5a21b"/><circle cx="6" cy="6" r="2.2" fill="#fff"/></svg>Morgan City</li>
      <li><svg width="12" height="16" viewBox="0 0 12 16"><path d="M6 0a6 6 0 0 1 6 6c0 4.5-6 10-6 10S0 10.5 0 6a6 6 0 0 1 6-6z" fill="#f5a21b"/><circle cx="6" cy="6" r="2.2" fill="#fff"/></svg>Shenandoah</li>
      <li><svg width="12" height="16" viewBox="0 0 12 16"><path d="M6 0a6 6 0 0 1 6 6c0 4.5-6 10-6 10S0 10.5 0 6a6 6 0 0 1 6-6z" fill="#f5a21b"/><circle cx="6" cy="6" r="2.2" fill="#fff"/></svg>Denham Spring</li>
      <li><svg width="12" height="16" viewBox="0 0 12 16"><path d="M6 0a6 6 0 0 1 6 6c0 4.5-6 10-6 10S0 10.5 0 6a6 6 0 0 1 6-6z" fill="#f5a21b"/><circle cx="6" cy="6" r="2.2" fill="#fff"/></svg>Lake Charles</li>
    </ul>
    <a class="btn btn-green" href="#">Contact Us</a>
  </div>
</section>

<section class="section why">
  <div class="photo" role="img" aria-label="Arborist in a bucket lift trimming tall trees"></div>
  <div class="why-panel">
    <h2 class="h-tech">Why Choose Us?</h2>
    <ul class="why-list">
      <li><svg width="14" height="14" viewBox="0 0 14 14"><path d="M2 7 L6 11 L12 3" fill="none" stroke="#79b23a" stroke-width="2.4"/></svg>Locally Owned &amp; Operated</li>
      <li><svg width="14" height="14" viewBox="0 0 14 14"><path d="M2 7 L6 11 L12 3" fill="none" stroke="#79b23a" stroke-width="2.4"/></svg>Licensed &amp; Insured</li>
      <li><svg width="14" height="14" viewBox="0 0 14 14"><path d="M2 7 L6 11 L12 3" fill="none" stroke="#79b23a" stroke-width="2.4"/></svg>Safety Is Our No.1 Priority</li>
      <li><svg width="14" height="14" viewBox="0 0 14 14"><path d="M2 7 L6 11 L12 3" fill="none" stroke="#79b23a" stroke-width="2.4"/></svg>Professional Work</li>
      <li><svg width="14" height="14" viewBox="0 0 14 14"><path d="M2 7 L6 11 L12 3" fill="none" stroke="#79b23a" stroke-width="2.4"/></svg>Licensed Arborist on Staff</li>
      <li><svg width="14" height="14" viewBox="0 0 14 14"><path d="M2 7 L6 11 L12 3" fill="none" stroke="#79b23a" stroke-width="2.4"/></svg>Free Estimates</li>
      <li><svg width="14" height="14" viewBox="0 0 14 14"><path d="M2 7 L6 11 L12 3" fill="none" stroke="#79b23a" stroke-width="2.4"/></svg>24-Hours Emergency Services</li>
    </ul>
    <a class="btn btn-orange" href="#">Contact Us</a>
  </div>
</section>

<section class="section blog">
  <h2 class="section-title h-tech">Latest Blog Posts</h2>
  <article class="post post-a">
    <div class="thumb" role="img" aria-label="Cut logs lying on a lawn after a removal" style="background:linear-gradient(135deg,#5d4a32,#a08760)"></div>
    <div class="body">
      <span class="date"><svg width="12" height="12" viewBox="0 0 12 12"><rect x="1" y="2" width="10" height="9" fill="none" stroke="#79b23a" stroke-width="1.4"/><path d="M1 5 H11" stroke="#79b23a" stroke-width="1.4"/></svg>12.08.2024</span>
      <h3>Dolor Sit Amet Lorem Ipsum Ctetuer Conse Adipis.</h3>
      <p>Fusce ac quam sit amet tempor tincidunt. Quisque vel ornare augue, sed dictum ante porttitor eget.</p>
    </div>
  </article>
  <article class="post post-b">
    <div class="thumb" role="img" aria-label="Fallen tree across a yard after a storm" style="background:linear-gradient(135deg,#4d6a36,#9db27a)"></div>
    <div class="body">
      <span class="date"><svg width="12" height="12" viewBox="0 0 12 12"><rect x="1" y="2" width="10" height="9" fill="none" stroke="#79b23a" stroke-width="1.4"/><path d="M1 5 H11" stroke="#79b23a" stroke-width="1.4"/></svg>11.06.2024</span>
      <h3>Dolor Sit Amet Lorem Ipsum Conse Ctetuer Adipis.</h3>
      <p>Fusce ac quam sit amet tempor tincidunt. Quisque vel ornare augue, sed dictum ante porttitor eget.</p>
    </div>
  </article>
  <article class="post post-c">
    <div class="thumb" role="img" aria-label="Climber roped into a tall tree trunk" style="background:linear-gradient(135deg,#3f4f2e,#b48a4f)"></div>
    <div class="body">
      <span class="date"><svg width="12" height="12" viewBox="0 0 12 12"><rect x="1" y="2" width="10" height="9" fill="none" stroke="#79b23a" stroke-width="1.4"/><path d="M1 5 H11" stroke="#79b23a" stroke-width="1.4"/></svg>10.11.2017</span>
      <h3>Dolor Sit Amet Lorem Ipsum Ctetuer Conse Adipis Dolor Ipsum.</h3>
      <p>Lorem ipsum dolor sit amet, consectetur adipiscing elit. Fusce ac quam sit amet tempor tincidunt. Quisque vel ornare augue, sed dictum ante porttitor eget. Nam quis tortor at sem vehicula rutrum.</p>
    </div>
  </article>
  <a class="btn btn-green" href="#">View All Blogs</a>
</section>

<section class="section contact">
  <div class="photo" role="img" aria-label="Soft sunlit forest backdrop"></div>
  <h2 class="contact-title h-tech" style="left:140px">Contact Us</h2>
  <h2 class="contact-title h-tech" style="left:670px">Quick Inquiry</h2>
  <div class="contact-card">
    <div class="person" role="img" aria-label="Friendly estimator wearing a yellow hard hat"></div>
    <div class="contact-info">
      <h4>Free Estimate From DELACROIX</h4>
      <div class="contact-row"><span class="ico"><svg width="12" height="14" viewBox="0 0 12 16"><path d="M6 0a6 6 0 0 1 6 6c0 4.5-6 10-6 10S0 10.5 0 6a6 6 0 0 1 6-6z" fill="#fff"/></svg></span><span>418 Cypress Bend Road<br>Lafayette, Louisiana</span></div>
      <div class="contact-row"><span class="ico"><svg width="12" height="12" viewBox="0 0 12 12"><path d="M2 1 L4.5 1 L5.5 4 L4 5 Q5 7.5 7 8 L8 6.5 L11 7.5 L11 10 Q6 11.5 2 6 Q0.5 3 2 1Z" fill="#fff"/></svg></span><span>(337) 555-0142<br>(337) 555-0187</span></div>
      <div class="contact-row"><span class="ico"><svg width="12" height="10" viewBox="0 0 12 10"><rect x="0.5" y="0.5" width="11" height="9" fill="none" stroke="#fff"/><path d="M0.5 0.5 L6 5.5 L11.5 0.5" fill="none" stroke="#fff"/></svg></span><span>E-Mail<br>hello@verdelltreecare.com</span></div>
      <div class="contact-row"><span class="ico"><svg width="12" height="12" viewBox="0 0 12 12"><circle cx="6" cy="6" r="5" fill="none" stroke="#fff" stroke-width="1.4"/><path d="M6 3 V6 L8 7.5" fill="none" stroke="#fff" stroke-width="1.4"/></svg></span><span><strong>Reachable for You</strong><br>Mo. - Fr.: 8:00 AM - 5:00 PM</span></div>
    </div>
  </div>
  <form class="inquiry">
    <div class="field">Name</div>
    <div class="field">Email</div>
    <div class="field">Phone</div>
    <div class="field message">Message</div>
    <span class="btn btn-green">Submit Now</span>
  </form>
</section>

<footer class="section site-footer">
  <svg class="footer-curve" width="1200" height="80" viewBox="0 0 1200 80">
    <path d="M0 20 Q600 110 1200 20 L1200 80 L0 80 Z" fill="#3c4241"/>
    <path d="M0 14 Q600 104 1200 14" fill="none" stroke="#f5a21b" stroke-width="6"/>
  </svg>
  <div class="footer-inner">
    <div class="brand"><span class="brand-mark"></span>Verdell Tree Care</div>
    <nav class="footer-nav"><span>Home</span><span>About Us</span><span>Services</span><span>Blog</span><span>Contact Us</span></nav>
    <div class="footer-base">
      <span>© 2024 Verdell Tree Care. All Rights Reserved</span>
      <div class="socials"><span></span><span></span><span></span></div>
    </div>
  </div>
</footer>

</body>
</html>
```